Birchline Septic Solutions

Would like to see some single sided ones but would also like to see some double sided with one sided only being the logo. Owners name is Colin Vandro. Phone number is 555-214-0387
Services are pumping, inspections, installs, and repairs

Contact Information for Business Card

555-241-0387 Colin Vandro Ridgeport, OH

```html
<!DOCTYPE html>
<html lang="en">
<head>
<meta charset="utf-8">
<title>Birchline Septic Solutions – Business Cards</title>
<link rel="stylesheet" href="https://fonts.googleapis.com/css2?family=Montserrat:wght@400;500;700;800&display=swap">
<style>
  :root {
    --backdrop: #4a4a49;
    --card: #161616;
    --teal: #2dbdb6;
    --white: #ffffff;
  }
  * { box-sizing: border-box; margin: 0; padding: 0; }
  html, body {
    width: 1200px; height: 801px; overflow: hidden;
    background: var(--backdrop);
    font-family: "Montserrat", sans-serif;
  }
  .stage {
    position: relative; width: 1200px; height: 801px;
    display: flex; align-items: center; justify-content: center; gap: 40px;
  }
  .card {
    position: relative; width: 540px; height: 309px;
    background: var(--card); border-radius: 16px; overflow: hidden;
    box-shadow: 0 10px 30px rgba(0,0,0,.35);
  }
  .card--front { border-bottom: 3px solid var(--teal); }
  .card--back { border-bottom: 3px solid var(--teal); }

  .swoosh { position: absolute; inset: 0; width: 100%; height: 100%; }

  .brand-name {
    color: var(--white); font-weight: 800; text-transform: uppercase;
    line-height: 1.05; letter-spacing: 1px;
  }
  .card--front .brand-name {
    position: absolute; left: 30px; top: 100px; width: 210px; font-size: 26px;
  }
  .divider {
    position: absolute; left: 258px; top: 52px; width: 2px; height: 150px;
    background: var(--teal);
  }
  .contact {
    position: absolute; left: 278px; top: 44px; color: var(--white);
  }
  .contact__name { color: var(--teal); font-weight: 700; font-size: 21px; line-height: 1.2; }
  .contact__town { font-size: 12px; margin-bottom: 14px; }
  .contact__list { list-style: none; font-size: 11.5px; line-height: 1.6; }
  .contact__list li { display: flex; align-items: center; gap: 7px; }
  .contact__list svg { width: 11px; height: 11px; flex: none; }
  .contact__address { font-size: 11.5px; line-height: 1.4; margin-top: 12px; }

  .card--back .brand-name {
    position: absolute; left: 0; right: 0; top: 84px;
    text-align: center; font-size: 42px;
  }
  .tagline {
    position: absolute; left: 0; right: 0; bottom: 40px;
    text-align: center; color: var(--teal); font-size: 16px; font-weight: 500;
  }
</style>
</head>
<body>
<main class="stage">
  <section class="card card--front" aria-label="Business card front">
    <svg class="swoosh" viewBox="0 0 540 309" preserveAspectRatio="none" aria-hidden="true">
      <path d="M150 309 C330 300 450 170 540 24 L540 309 Z" fill="var(--white)"/>
      <path d="M175 309 C350 302 462 185 540 40 L540 309 Z" fill="var(--card)"/>
      <path d="M190 309 C360 304 470 200 540 52 L540 309 Z" fill="var(--teal)"/>
    </svg>
    <p class="brand-name">Birchline Septic Solutions</p>
    <span class="divider"></span>
    <div class="contact">
      <p class="contact__name">Colin Vandro</p>
      <p class="contact__town">Ridgeport</p>
      <ul class="contact__list">
        <li><svg viewBox="0 0 24 24"><path fill="var(--teal)" d="M6.6 10.8a15 15 0 0 0 6.6 6.6l2.2-2.2c.3-.3.7-.4 1-.2 1.1.4 2.3.6 3.6.6.6 0 1 .4 1 1V20c0 .6-.4 1-1 1A17 17 0 0 1 3 4c0-.6.4-1 1-1h3.5c.6 0 1 .4 1 1 0 1.3.2 2.5.6 3.6.1.3 0 .7-.2 1z"/></svg>555-214-0387</li>
        <li><svg viewBox="0 0 24 24"><path fill="var(--teal)" d="M2 5h20v14H2z"/><path fill="none" stroke="var(--card)" stroke-width="2" d="M2 6l10 7 10-7"/></svg>info@birchlinemail.com</li>
        <li><svg viewBox="0 0 24 24"><circle cx="12" cy="12" r="10" fill="var(--teal)"/><path fill="none" stroke="var(--card)" stroke-width="1.5" d="M2 12h20M12 2c3 3 3 17 0 20M12 2c-3 3-3 17 0 20"/></svg>www.birchlineseptic.com</li>
      </ul>
      <p class="contact__address">Your address, City<br>State, Zip 1234</p>
    </div>
  </section>

  <section class="card card--back" aria-label="Business card back">
    <p class="brand-name">Birchline<br>Septic Solutions</p>
    <p class="tagline">Services are pumping, inspections, installs, and repairs</p>
  </section>
</main>
</body>
</html>
```